Fresh, modern, fun business card for pediatric dental practice

Need a business card for fresh, modern, fun pediatric dental practice

Clean look that matches our website's font and colors

We prefer the look of curved corners on business cards

Target Market(s)

parents (mothers) of young children, professionals, mid-high class

Industry/Entity Type

Dental

Contact Information for Business Card

Maplebrook Pediatric Dentistry
482 Quarry Lane
Suite 517
Cedarvale, PA 17590
717.555.0193
www.maplebrookkidsdental.example

Mei-Ran Tsai, DMD
Corinne Walbeck, DMD
(we are working on our email address, but we would like that on the card as well)

Font styles to use
Sans Serif

Requirements
Must have
• All info; we would also like to make cards for individual staff members
• colors from our website and color palatte, attatched
• use same font and design as website for branding
Nice to have
• clean, simple card that has a pop of color
• we would like to see a few designs with our tag line "where smiles get brighter"
• we are not sure if we want to have it on there or not
• we would like to see a few designs incorporating the ribbon graphic on our website where the word WELCOME is

```html
<!DOCTYPE html>
<html lang="en">
<head>
<meta charset="UTF-8">
<title>Maplebrook Pediatric Dentistry – Business Card</title>
<link href="https://fonts.googleapis.com/css2?family=Lato:wght@400;700&display=swap" rel="stylesheet">
<style>
  :root {
    --stage: #1b1b1b;
    --card: #2a2a2a;
    --card-edge: #333333;
    --sun: #f5b51f;
    --berry: #d9378f;
    --ink: #f2f2f2;
    --muted: #d8d8d8;
  }
  * { box-sizing: border-box; margin: 0; padding: 0; }
  html, body {
    width: 1200px; height: 900px; overflow: hidden;
    background: var(--stage);
    font-family: "Lato", sans-serif;
  }
  .stage {
    width: 1200px; height: 900px;
    display: flex; flex-direction: column; align-items: center; justify-content: center;
    gap: 40px;
  }
  .card {
    width: 700px; height: 400px;
    background: var(--card);
    border: 1px solid var(--card-edge);
    border-radius: 22px;
    position: relative;
    box-shadow: 0 10px 30px rgba(0,0,0,.55);
  }

  /* Back of card */
  .card-back { display: flex; flex-direction: column; align-items: center; justify-content: center; gap: 56px; }
  .brand { display: flex; align-items: center; gap: 16px; }
  .brand-dot { width: 30px; height: 30px; border-radius: 50%; background: var(--sun); flex: none; }
  .brand-name { font-weight: 700; color: var(--sun); line-height: 1.05; }
  .card-back .brand-name { font-size: 46px; color: var(--muted); }
  .card-back .brand-dot { background: var(--muted); width: 40px; height: 40px; }
  .brand-name small { display: block; font-size: .52em; letter-spacing: 2px; }
  .back-url { font-size: 19px; letter-spacing: 2px; color: var(--ink); }
  .back-url .domain { color: var(--sun); }

  /* Front of card */
  .card-front { display: flex; align-items: center; padding: 0 40px 0 48px; }
  .card-front .brand { width: 300px; }
  .card-front .brand-name { font-size: 36px; }
  .divider { width: 2px; height: 220px; background: var(--berry); margin: 0 34px 0 22px; flex: none; }
  .details { color: var(--ink); font-size: 17px; line-height: 1.35; }
  .person-name { color: var(--sun); font-weight: 700; font-size: 25px; letter-spacing: 2px; }
  .person-title { font-size: 18px; margin-bottom: 14px; }
  .practice { color: var(--sun); }
  .address { margin-bottom: 12px; }
  .contact-line { display: flex; align-items: center; gap: 10px; }
  .contact-line svg { width: 15px; height: 15px; flex: none; }
</style>
</head>
<body>
<main class="stage">

  <section class="card card-back" aria-label="Card back">
    <div class="brand">
      <span class="brand-dot"></span>
      <p class="brand-name">Maplebrook<small>Pediatric Dentistry</small></p>
    </div>
    <p class="back-url">www.<span class="domain">maplebrookkidsdental</span>.example</p>
  </section>

  <section class="card card-front" aria-label="Card front">
    <div class="brand">
      <span class="brand-dot"></span>
      <p class="brand-name">Maplebrook<small>Pediatric Dentistry</small></p>
    </div>
    <span class="divider"></span>
    <div class="details">
      <p class="person-name">CORINNE WALBECK</p>
      <p class="person-title">DMD</p>
      <p class="practice">Maplebrook Pediatric Dentistry</p>
      <p class="address">482 Quarry Lane<br>Suite 517 Cedarvale, PA 17590</p>
      <p class="contact-line">
        <svg viewBox="0 0 16 16" aria-hidden="true"><path fill="#f5b51f" d="M3.6 1.2l2.2 2.6-1.3 1.6c.9 2 2.3 3.4 4.1 4.3l1.6-1.3 2.6 2.2-1.3 2.2C7.3 13 3 8.7 1.4 2.5z"/></svg>
        717.555.0193
      </p>
      <p class="contact-line">
        <svg viewBox="0 0 16 16" aria-hidden="true"><rect x="1" y="3" width="14" height="10" rx="1" fill="#f5b51f"/><path d="M1.5 3.5L8 9l6.5-5.5" fill="none" stroke="#2a2a2a" stroke-width="1.3"/></svg>
        info@maplebrookkidsdental.example
      </p>
      <p class="contact-line">
        <svg viewBox="0 0 16 16" aria-hidden="true"><g fill="none" stroke="#f5b51f" stroke-width="1.3"><circle cx="8" cy="8" r="6.5"/><ellipse cx="8" cy="8" rx="3" ry="6.5"/><path d="M1.5 8h13M2.5 4.8h11M2.5 11.2h11"/></g></svg>
        www.maplebrookkidsdental.example
      </p>
    </div>
  </section>

</main>
</body>
</html>
```